Computer Training in the Education sector - Letterhead

We need a new letter head to be designed for the company. We provide computer training fro the Education Sector, both primary and private tertiary providers. The colours will need to tie in with the website www.crossingthestream.co.nz.
The company name is Crossing the Stream with the tag line of Computer Training for Educators.
The footer will need to have the following detail...
0508 PCS MENTOR
021 839 415
www.crossingthestream.co.nz / training@crossingthestream.co.nz
Updates

Thanks for the designs so far.

Some have watermarks in the background. Please don't worry about using watermarks as I will not be using a watermark in in a final design.
Regards,
Roger

Thank you for all the designs and the effort. There was some great concepts that came through.

Cheers
Roger

Industry/Entity Type

Computer

```html
<!DOCTYPE html>
<html lang="en">
<head>
<meta charset="utf-8">
<title>Crossing the Stream – Letterhead</title>
<link rel="stylesheet" href="https://fonts.googleapis.com/css2?family=Arimo:wght@400&family=Questrial&display=swap">
<style>
  :root {
    --backdrop: #a9a9a9;
    --paper: #ffffff;
    --brand-blue: #2f6cb5;
    --brand-orange: #ee8a2a;
    --ink: #161616;
    --sky-pale: #e3edf6;
    --sky-soft: #f1f6fb;
    --signature-tone: #e2e2e2;
  }
  * { margin: 0; padding: 0; box-sizing: border-box; }
  html, body {
    width: 1200px; height: 848px; overflow: hidden;
    background: var(--backdrop);
  }
  .letterhead {
    position: absolute; left: 330px; top: 42px;
    width: 540px; height: 764px;
    background: var(--paper);
    box-shadow: 0 2px 6px rgba(0,0,0,0.25);
    font-family: "Arimo", Arial, sans-serif;
    color: var(--ink);
  }
  .sky-area {
    position: absolute;
    background: linear-gradient(180deg, var(--sky-soft), var(--sky-pale));
  }
  .sky-area--top-centre { left: 228px; top: 20px; width: 120px; height: 40px; }
  .sky-area--top-right { left: 432px; top: 16px; width: 92px; height: 28px; }
  .sky-area--under-brand { left: 66px; top: 126px; width: 132px; height: 42px; }

  .brand {
    position: absolute; left: 36px; top: 56px;
    display: flex; align-items: center; gap: 7px;
  }
  .brand__dot {
    width: 12px; height: 12px; border-radius: 50%;
    background: var(--brand-orange);
    flex: none;
  }
  .brand__name {
    font-family: "Questrial", "Century Gothic", sans-serif;
    font-size: 18px; line-height: 20px;
    color: var(--brand-blue);
    width: 80px;
  }
  .tagline {
    position: absolute; right: 54px; top: 70px;
    text-align: right;
    font-family: "Questrial", "Century Gothic", sans-serif;
    font-size: 13px; line-height: 16px;
    color: var(--brand-blue);
    letter-spacing: -0.2px;
  }
  .letter-body {
    position: absolute; left: 146px; top: 181px; width: 358px;
    font-size: 7.2px; line-height: 11.4px;
    text-align: justify;
    color: var(--ink);
    filter: grayscale(100%);
    -webkit-font-smoothing: antialiased;
  }
  .letter-body p + p { margin-top: 11.4px; }
  .signature {
    position: absolute; left: 140px; top: 504px;
    width: 144px; height: 42px;
    background: linear-gradient(90deg, var(--signature-tone), #f4f4f4);
  }
  .contact {
    position: absolute; left: 44px; top: 648px;
    font-size: 6.4px; line-height: 12px;
    color: var(--ink);
    filter: grayscale(0%);
    -webkit-font-smoothing: antialiased;
  }
  .contact__line { display: flex; align-items: center; gap: 4px; }
  .contact__badge {
    display: inline-block; width: 9px; height: 9px;
    background: var(--brand-blue); color: #fff;
    font-size: 6px; line-height: 9px; text-align: center;
  }
  .contact__web {
    display: block; margin-top: 7px;
    background: var(--brand-orange); color: #fff;
    padding: 0 4px; font-size: 6.4px; line-height: 9px; width: 100px;
  }
</style>
</head>
<body>
  <main class="letterhead">
    <div class="sky-area sky-area--top-centre" role="img" aria-label="Soft illustrated cloud"></div>
    <div class="sky-area sky-area--top-right" role="img" aria-label="Soft illustrated cloud"></div>
    <div class="sky-area sky-area--under-brand" role="img" aria-label="Soft illustrated cloud"></div>

    <header>
      <div class="brand">
        <span class="brand__dot"></span>
        <span class="brand__name">Crossing the Stream</span>
      </div>
      <div class="tagline">Computer Training<br>for Educators</div>
    </header>

    <section class="letter-body">
      <p>Lorem ipsum dolor sit amet, consectetur adipiscing elit. Suspendisse blandit, nulla ut porta scelerisque, urna massa ultrices ligula, at rutrum nunc ipsum ac risus. Sed consectetur nulla non velit sollicitudin a eleifend tortor pellentesque. Cras laoreet iaculis pretium. Vestibulum vitae sapien at metus fermentum tempus quis sed mauris. Donec blandit metus in nibh laoreet ultrices. Nullam molestie, turpis ac adipiscing tincidunt, urna justo eleifend ligula, et consectetur massa lorem ac risus. Aenean quis justo vitae massa accumsan ultricies posuere eget diam. Aenean ipsum sapien, pellentesque id semper vitae, mattis eget enim. Vestibulum congue tincidunt enim ut tristique. Praesent interdum malesuada adipiscing. Donec quis felis massa.</p>
      <p>Praesent nisi libero, pretium eu interdum eu, rhoncus ut lorem. Praesent faucibus lorem sit amet ligula consequat adipiscing. Morbi adipiscing dapibus erat, eu condimentum nibh vestibulum vel. In elementum nulla id arcu bibendum malesuada. Donec non nulla sit amet tortor volutpat placerat id vel felis. Maecenas accumsan, augue ac molestie iaculis, justo risus vestibulum dolor, eu ullamcorper nulla orci ac est. Donec tristique sem a nisl euismod convallis id ac lacus. Sed pretium bibendum velit eget mollis. Praesent porta suscipit lacus, ac porta odio faucibus eu. Donec accumsan laoreet nisi et hendrerit. In fringilla enim ac urna sagittis convallis.</p>
      <p>Nullam est mi, euismod ac pretium ac, consequat eu urna. Aliquam egestas, elit non gravida pellentesque, purus orci facilisis est, vitae ultricies turpis nisl non justo. Fusce varius libero nec nibh elementum consequat ut sed elit. Integer lorem erat, varius ac malesuada vitae, convallis sit amet libero. Cras sagittis, urna eu scelerisque auctor, elit tellus vestibulum mi, non elementum metus eros ut dolor. Etiam porta est dolor. Vivamus suscipit lobortis commodo. Integer convallis, nunc tincidunt rhoncus lobortis, sapien purus ultrices orci, quis dignissim urna felis dictum elit.</p>
    </section>

    <div class="signature" role="img" aria-label="Handwritten signature of the sender"></div>

    <footer class="contact">
      <div>0508 PCS MENTOR</div>
      <div class="contact__line"><span class="contact__badge">p.</span>021 839 415</div>
      <div class="contact__line"><span class="contact__badge">m.</span>training@crossingthestream.co.nz</div>
      <div class="contact__web">www.crossingthestream.co.nz</div>
    </footer>
  </main>
</body>
</html>
```